A private security company called "Tavron Security Services Ltd"

Hello everybody,

We need a web page for a company based in NZ. It is mainly an informative website so it would be wonderful if the designer puts their absolute best into making it a website that I would really appreciate. The website needs to show professionalism and also needs to make our web surfers find the information they need in a click. the company's colour is black and silver, and if those two colours could be integrated into the website it would be absolutely lovely. Please do contact me for any information.

Sincerely,
Dorian Vaskel

Industry/Entity Type

Security

```html
<!DOCTYPE html>
<html lang="en">
<head>
<meta charset="utf-8">
<title>Tavron Security Services Ltd</title>
<link href="https://fonts.googleapis.com/css2?family=Open+Sans:wght@300;400;600;700&display=swap" rel="stylesheet">
<style>
:root{
  --dark:#272727;
  --darker:#1c1c1c;
  --red:#c20000;
  --silver:#e6e6e6;
  --text:#777;
  --heading:#333;
  --foot-text:#bdbdbd;
}
*{box-sizing:border-box;margin:0;padding:0}
html,body{width:894px;height:1200px;overflow:hidden;background:#fff;font-family:'Open Sans',sans-serif}
.page{position:relative;width:894px;height:1200px}
.abs{position:absolute}
.header-band{left:0;top:0;width:894px;height:332px;background:var(--dark)}
.brand{left:82px;top:40px;display:flex;align-items:center;gap:8px;color:#fff;font-weight:600;font-size:12px;letter-spacing:.5px;text-transform:uppercase;line-height:1.3}
.brand-mark{width:22px;height:22px;background:#fff;flex:none}
.call{left:646px;top:12px;color:#fff;font-size:14px}
.search{left:646px;top:35px;width:167px;height:24px;background:#1e1e1e;color:#666;font-size:9px;font-style:italic;padding:6px 8px}
.nav-rule{left:298px;top:69px;width:515px;height:1px;background:#444}
.nav{left:298px;top:78px;display:flex;height:20px}
.nav a{color:#fff;text-decoration:none;font-size:10.5px;line-height:20px;padding:0 6px;margin-right:12.5px;white-space:nowrap}
.nav a.active{background:var(--red)}
.nav a:last-child{margin-right:0}
.hero{left:82px;top:107px;width:731px;height:255px;background:radial-gradient(ellipse at 30% 30%,#f3f3f3,#d9d9d9 70%,#cfcfcf)}
.hero-photo{left:398px;top:0;width:333px;height:255px;background:radial-gradient(ellipse at 60% 45%,#c9c9c4,#b5b5ae 45%,rgba(210,210,210,0) 75%)}
.hero h1{left:21px;top:47px;font-size:27px;font-weight:600;color:#333;line-height:34px}
.hero h2{left:21px;top:81px;font-size:27px;font-weight:300;color:#333;line-height:34px}
.hero p{left:21px;top:122px;width:300px;font-size:10.5px;line-height:15px;color:#666}
.btn{display:block;background:var(--red);color:#fff;font-size:11.5px;font-weight:600;text-decoration:none;padding-left:13px;clip-path:polygon(0 0,88% 0,100% 50%,88% 100%,0 100%)}
.hero .btn{left:21px;top:163px;width:97px;height:27px;line-height:27px}
.card{top:384px;width:174px}
.card-title{height:32px;background:var(--red);color:#fff;font-weight:600;font-size:13px;text-align:center;line-height:32px;white-space:nowrap}
.card-photo{height:104px}
.card p{margin-top:13px;font-size:9.5px;line-height:15px;color:var(--text);width:176px}
.card .btn{margin-top:12px;width:97px;height:28px;line-height:28px}
.intro{left:82px;top:632px;width:731px;height:75px;background:#f1f1f1;border:1px solid #e2e2e2;border-radius:2px}
.intro h3{left:12px;top:12px;font-size:13px;font-weight:600;color:var(--heading)}
.intro p{left:13px;top:32px;width:560px;font-size:9px;line-height:15px;color:#888}
.btn-dark{left:575px;top:22px;width:145px;height:31px;background:#2b2b2b;border-radius:3px;color:#fff;font-size:11.5px;font-weight:600;text-align:center;line-height:31px}
.about h3{left:82px;top:730px;font-size:13px;font-weight:600;color:var(--heading)}
.about p{left:82px;width:380px;font-size:9.5px;line-height:15px;color:#888}
.about .btn{left:82px;top:908px;width:97px;height:27px;line-height:27px}
.video{left:474px;top:731px;width:339px;height:205px;background:linear-gradient(180deg,#8a9bb0,#6f7f92 55%,#3f4752)}
.play{left:145px;top:77px}
.footer{left:0;top:962px;width:894px;height:203px;background:var(--dark)}
.col-rule{top:0;width:1px;height:203px;background:#1a1a1a}
.footer h4{top:18px;color:#fff;font-size:13px;font-weight:600}
.footer ul{list-style:none;top:45px}
.footer li{font-size:10px;line-height:16.4px;color:var(--foot-text)}
.quote{left:396px;top:45px;width:195px;font-size:10px;line-height:16.4px;color:var(--foot-text)}
.quote u{color:#fff;display:block;margin-top:3px}
.field{left:637px;width:166px;background:var(--darker);color:#777;font-size:9px;font-style:italic;padding:6px 9px}
.send{left:733px;top:158px;width:70px;height:27px;background:linear-gradient(#fff,#d8d8d8);border-radius:2px;color:#333;font-size:11px;font-weight:600;text-align:center;line-height:27px}
.copy{left:0;top:1174px;width:894px;text-align:center;font-size:9.5px;color:#333}
</style>
</head>
<body>
<div class="page">
  <div class="abs header-band"></div>
  <div class="abs brand"><span class="brand-mark"></span><span>Tavron<br>Security Services Ltd.</span></div>
  <div class="abs call">CALL : 0800-555-0142</div>
  <div class="abs search">Search here...</div>
  <div class="abs nav-rule"></div>
  <nav class="abs nav">
    <a class="active" href="#">HOME</a><a href="#">ABOUT US</a><a href="#">SECURITY SYSTEM</a><a href="#">SPECIALIZED SECURITY</a><a href="#">CARRERS</a><a href="#">CONTACT US</a>
  </nav>

  <section class="abs hero">
    <div class="abs hero-photo" role="img" aria-label="Cluster of CCTV cameras mounted on a pole"></div>
    <h1 class="abs">Newzealand’s Best</h1>
    <h2 class="abs">Security Company</h2>
    <p class="abs">Lorem ipsum dolor sit amet, consectetur adipisicing elit, sed do eiusmod tempor incididunt dolore magna aliqua..</p>
    <a class="abs btn" href="#">Learn More</a>
  </section>

  <div class="abs card" style="left:82px">
    <div class="card-title">Property Guards</div>
    <div class="card-photo" role="img" aria-label="Guard in black security jacket" style="background:linear-gradient(135deg,#4a4f55,#1f2226)"></div>
    <p>Lorem ipsum dolor sit amet, consecte-tur adipisicing elit, sed do eiusmod tempor incididunt magna aliqua..</p>
    <a class="btn" href="#">Learn More</a>
  </div>
  <div class="abs card" style="left:268px">
    <div class="card-title">Corporate Events Security</div>
    <div class="card-photo" role="img" aria-label="Event staff and officers at a crowd" style="background:linear-gradient(135deg,#b8b8b0,#5a5a58 60%,#2a2a2a)"></div>
    <p>Lorem ipsum dolor sit amet, consecte-tur adipisicing elit, sed do eiusmod tempor incididunt magna aliqua..</p>
    <a class="btn" href="#">Learn More</a>
  </div>
  <div class="abs card" style="left:453px">
    <div class="card-title">Security Consultancy</div>
    <div class="card-photo" role="img" aria-label="Consultants at a wall of monitoring screens" style="background:linear-gradient(135deg,#9a9a98,#4a4a48 60%,#2a2a2a)"></div>
    <p>Lorem ipsum dolor sit amet, consecte-tur adipisicing elit, sed do eiusmod tempor incididunt magna aliqua..</p>
    <a class="btn" href="#">Learn More</a>
  </div>
  <div class="abs card" style="left:639px">
    <div class="card-title">Private Investigation</div>
    <div class="card-photo" role="img" aria-label="Investigator typing at a keyboard in blue light" style="background:linear-gradient(135deg,#1a3a7a,#5a86c8 55%,#20355f)"></div>
    <p>Lorem ipsum dolor sit amet, consecte-tur adipisicing elit, sed do eiusmod tempor incididunt magna aliqua..</p>
    <a class="btn" href="#">Learn More</a>
  </div>

  <section class="abs intro">
    <h3 class="abs">TAVRON SECURITY SERVICES LTD</h3>
    <p class="abs">Lorem ipsum dolor sit amet, consectetur adipisicing elit, sed do eiusmod tempor incididunt ut labore et dolore magna aliqua. Ut enim ad minim veniam, quis nostrud exercitation ullamco laboris nisi ut aliquip ex ea commodo consequat.</p>
    <div class="abs btn-dark">Click here to Learn More</div>
  </section>

  <section class="about">
    <h3 class="abs">ABOUT US</h3>
    <p class="abs" style="top:755px">Lorem ipsum dolor sit amet, consectetur adipisicing elit, sed do eiusmod tempor incidi-dunt ut labore et dolore magna aliqua. Ut enim ad minim veniam, quis nostrud exercita-tion ullamco laboris nisi ut aliquip ex ea commodo consequat.</p>
    <p class="abs" style="top:811px">Duis aute irure dolor in reprehenderit in voluptate velit esse cillum dolore eu fugiat nulla pariatur. Excepteur sint occaecat cupidatat non proident, sunt in culpa qui officia dese-runt mollit anim id est laborum.</p>
    <p class="abs" style="top:866px">Ut enim ad minim veniam, quis nostrud exercitation ullamco laboris nisi ut aliquip ex ea commodo consequat..</p>
    <a class="abs btn" href="#">Learn More</a>
    <div class="abs video" role="img" aria-label="Video: operator with headset watching CCTV monitors in a control room">
      <svg class="abs play" width="50" height="50" viewBox="0 0 50 50"><circle cx="25" cy="25" r="25" fill="rgba(30,30,30,.75)"/><path d="M19 14 L36 25 L19 36 Z" fill="#ddd"/></svg>
    </div>
  </section>

  <footer class="abs footer">
    <div class="abs col-rule" style="left:202px"></div>
    <div class="abs col-rule" style="left:365px"></div>
    <div class="abs col-rule" style="left:607px"></div>
    <h4 class="abs" style="left:81px">SITE MAP</h4>
    <ul class="abs" style="left:81px"><li>Home</li><li>About Us</li><li>Security System</li><li>Specialized Security</li><li>Carrers</li><li>Contact Us</li></ul>
    <h4 class="abs" style="left:234px">LINKS</h4>
    <ul class="abs" style="left:234px"><li>Lorem ipsum</li><li>Dolor sit Amet</li><li>consectetur aDipsicing</li><li>Elit, Sed Do Euismod</li><li>Tempor incidunt</li><li>Magna Aliqua</li></ul>
    <h4 class="abs" style="left:396px">TESTIMONIALS</h4>
    <p class="abs quote">“Lorem ipsum dolor sit amet, consectetur adipisicing elit, sed do eiusmod tempor incididunt magna aliqua”<u>Mara Ellison</u></p>
    <h4 class="abs" style="left:635px">QUICK CONTACT</h4>
    <div class="abs field" style="top:47px;height:24px">Name</div>
    <div class="abs field" style="top:75px;height:24px">Email</div>
    <div class="abs field" style="top:104px;height:46px">Message</div>
    <div class="abs send">SEND</div>
  </footer>
  <div class="abs copy">Copyrights © 2014 Tavron .com - All Rights Reserved</div>
</div>
</body>
</html>
```